Heritage Hollow Business Cards

Require a business card design. <br/><br/>Needs to include logo (either round or long version) plus these details:<br/>Maya Torvell<br/>Heritage Hollow<br/>maya@kelvadtrading.com.au<br/>02 6481 7395<br/>PO Box Glenwarra NSW 2791<br/>www.heritagehollow.com.au<br/><br/>I need in an editable format so that I can create for multiple staff members. <br/><br/>

Target Market(s)

We are an online store selling renovation products to home owners are builders. Looking for a classic classy design.

Industry/Entity Type

Home And Garden

Contact Information for Business Card

Maya Torvell
Heritage Hollow
maya@kelvadtrading.com.au
02 6481 7395
PO Box Glenwarra NSW 2791
www.heritagehollow.com.au

Colors

Designer to choose colors to be used in the design.

Requirements
Must have
• Must include Logo.

```html
<!DOCTYPE html>
<html lang="en">
<head>
<meta charset="utf-8">
<title>Heritage Hollow Business Cards</title>
<link href="https://fonts.googleapis.com/css2?family=Libre+Baskerville:wght@400;700&family=Open+Sans:wght@400&display=swap" rel="stylesheet">
<style>
  :root {
    --backdrop: #1c1c1c;
    --card: #ffffff;
    --ink: #2b2b2b;
    --accent: #4a6b5d;
    --faint: #ececec;
    --faint-edge: #f7f7f7;
  }
  * { box-sizing: border-box; margin: 0; padding: 0; }
  html, body { width: 1200px; height: 960px; overflow: hidden; background: var(--backdrop); }
  .canvas { position: relative; width: 1200px; height: 960px; }
  .card {
    position: absolute; left: 230px; width: 740px; height: 423px;
    background: var(--card); overflow: hidden;
  }
  .card--front { top: 40px; }
  .card--back { top: 497px; }

  .brand { display: flex; align-items: center; font-family: "Libre Baskerville", serif; font-weight: 700; color: var(--ink); }
  .brand-circle { border: 2px solid var(--ink); border-radius: 50%; flex: none; }

  .card--front .brand { position: absolute; left: 0; right: 0; top: 0; bottom: 0; justify-content: center; gap: 22px; font-size: 38px; }
  .card--front .brand-circle { width: 74px; height: 74px; }

  .card--back .brand { position: absolute; left: 40px; top: 30px; gap: 14px; font-size: 20px; }
  .card--back .brand-circle { width: 46px; height: 46px; }

  .brand-title {
    position: absolute; left: 40px; top: 110px;
    font-family: "Libre Baskerville", serif; font-size: 34px; color: var(--ink);
  }
  .house-sketch {
    position: absolute; left: 0; top: 200px; width: 340px; height: 223px;
    background: linear-gradient(160deg, var(--faint) 0%, var(--faint-edge) 100%);
  }

  .person { position: absolute; right: 62px; top: 180px; text-align: right; font-family: "Libre Baskerville", serif; }
  .person-name { font-size: 24px; font-weight: 700; color: var(--accent); }
  .person-role { font-size: 14px; font-weight: 700; color: var(--ink); margin-top: 4px; }
  .accent-tab {
    position: absolute; right: 0; top: 186px; width: 22px; height: 52px;
    background: var(--accent); border-radius: 12px 0 0 12px;
  }

  .contact { position: absolute; right: 62px; top: 262px; text-align: right; font-family: "Open Sans", sans-serif; font-size: 15px; color: var(--ink); line-height: 1.5; }
  .address { margin-bottom: 12px; }
  .contact-line { display: flex; justify-content: flex-end; align-items: center; gap: 8px; }
  .contact-line svg { width: 14px; height: 14px; fill: none; stroke: var(--accent); stroke-width: 1.6; }
</style>
</head>
<body>
<main class="canvas">
  <section class="card card--front" aria-label="Card front">
    <div class="brand"><span class="brand-circle"></span><span>Heritage Hollow</span></div>
  </section>

  <section class="card card--back" aria-label="Card back">
    <div class="brand"><span class="brand-circle"></span><span>Heritage Hollow</span></div>
    <div class="brand-title">Heritage Hollow</div>
    <div class="house-sketch" role="img" aria-label="Faint pencil sketch of a house roofline with chimney"></div>

    <div class="person">
      <div class="person-name">Maya Torvell</div>
      <div class="person-role">Director</div>
    </div>
    <div class="accent-tab"></div>

    <div class="contact">
      <div class="address">PO Box Glenwarra<br>NSW 2791</div>
      <div class="contact-line">
        <svg viewBox="0 0 16 16"><path d="M4 1.5l2.5 3-1.5 1.8c.9 2 2.5 3.6 4.5 4.5l1.8-1.5 3 2.5-1.6 2.2C7.5 14 2 8.5 1.8 3.1z"/></svg>
        <span>02 6481 7395</span>
      </div>
      <div class="contact-line">
        <svg viewBox="0 0 16 16"><rect x="1.5" y="3.5" width="13" height="9"/><path d="M1.5 3.5l6.5 5 6.5-5"/></svg>
        <span>maya@kelvadtrading.com.au</span>
      </div>
      <div class="contact-line">
        <svg viewBox="0 0 16 16"><circle cx="8" cy="8" r="6.5"/><ellipse cx="8" cy="8" rx="2.8" ry="6.5"/><path d="M1.5 8h13"/></svg>
        <span>www.heritagehollow.com.au</span>
      </div>
    </div>
  </section>
</main>
</body>
</html>
```